Roofing company in Toronto, Canada needs a logo design and business card design

We need a business card and logo created for our company. Our company is "KLV Roofing" which provides roofing services for commercial and residential customers. We serve customers in the Greater Toronto Area (in Canada) thus the name KLV.

We want the logo and business card to be a modern design displaying professionalism and quality in the work. We would prefer rounded corners for the business cards but are open to other ideas. The cards should be pleasant and appealing to customers.

Target Market(s)

Commercial and Residential customers

Industry/Entity Type

Roofing

Contact Information for Business Card

Logo Text

KLV Roofing

Requirements
Nice to have
• Colours that are pleasing to the eye but at the same time should stand out from other business cards. If the design can incorporate the name of KLV Roofing and the actual concept of roofing that would be nice.
Should not have
• Do not want the business cards or logo to be childish looking. Need to look professionally designed.

```html
<!DOCTYPE html>
<html lang="en">
<head>
<meta charset="utf-8">
<title>KLV Roofing – Business Card</title>
<link rel="stylesheet" href="https://fonts.googleapis.com/css2?family=PT+Sans:wght@400;700&display=swap">
<style>
  :root {
    --backdrop: #000000;
    --card: #333437;
    --gold: #e6ac12;
    --text: #f2f2f2;
    --grey: #d9d9d9;
    --rule: #45464a;
  }
  * { margin: 0; padding: 0; box-sizing: border-box; }
  html, body {
    width: 1200px; height: 900px; overflow: hidden;
    background: var(--backdrop);
    font-family: "PT Sans", Arial, sans-serif;
  }
  .canvas { position: relative; width: 1200px; height: 900px; }
  .card {
    position: absolute; top: 271px;
    width: 457px; height: 281px;
    background: var(--card);
    border-radius: 14px;
  }
  .card--front { left: 137px; }
  .card--back { left: 626px; }

  .front-brand {
    position: absolute; left: 30px; top: 108px;
    display: flex; align-items: center; gap: 10px;
  }
  .brand-square { width: 20px; height: 20px; background: var(--gold); }
  .brand-name {
    font-size: 28px; font-weight: 700; color: var(--gold);
    letter-spacing: 0.5px; white-space: nowrap;
  }

  .divider {
    position: absolute; left: 237px; top: 78px;
    width: 1px; height: 128px; background: var(--rule);
  }
  .contact { position: absolute; left: 249px; top: 64px; color: var(--text); }
  .contact__name { font-size: 19px; color: var(--gold); line-height: 24px; }
  .contact__title { font-size: 13px; line-height: 16px; margin-bottom: 12px; }
  .contact__address { font-size: 13px; line-height: 16px; margin-bottom: 10px; }
  .contact__list { list-style: none; font-size: 13px; line-height: 16.5px; }
  .contact__list li { display: flex; align-items: center; gap: 7px; }
  .contact__list svg { width: 10px; height: 10px; fill: var(--gold); flex: none; }

  .back-brand {
    position: absolute; inset: 0;
    display: flex; flex-direction: column; align-items: center; justify-content: center;
    font-weight: 700; color: var(--gold); line-height: 1;
  }
  .back-brand__main { font-size: 66px; letter-spacing: 2px; }
  .back-brand__sub { font-size: 34px; letter-spacing: 2px; margin-top: 4px; }
</style>
</head>
<body>
<main class="canvas">
  <section class="card card--front">
    <div class="front-brand">
      <span class="brand-square"></span>
      <span class="brand-name">KLV Roofing</span>
    </div>
    <div class="divider"></div>
    <div class="contact">
      <p class="contact__name">Daniel Carter</p>
      <p class="contact__title">Managing Director</p>
      <p class="contact__address">12345, Address Goes Here<br>Country Name, 123456.</p>
      <ul class="contact__list">
        <li><svg viewBox="0 0 10 10"><path d="M2 0.5 3.6 2.6 2.7 3.6C3.3 5 4.9 6.7 6.4 7.3L7.4 6.4 9.5 8 8.6 9.4C5 9.4 0.6 5 0.6 1.4Z"/></svg>044-987 654 321</li>
        <li><svg viewBox="0 0 10 10"><path d="M0.5 2H9.5V8H0.5Z M1 2.4 5 5.4 9 2.4" stroke="#333437" stroke-width="0.8"/></svg>info@klvroofing.ca</li>
        <li><svg viewBox="0 0 10 10"><path d="M4 6 6 4" stroke="#e6ac12" stroke-width="1.2" fill="none"/><path d="M5.5 2.5 6.8 1.2a1.8 1.8 0 0 1 2.5 2.5L8 5M4.5 7.5 3.2 8.8a1.8 1.8 0 0 1-2.5-2.5L2 5" stroke="#e6ac12" stroke-width="1.2" fill="none"/></svg>www.klvroofing.ca</li>
      </ul>
    </div>
  </section>

  <section class="card card--back">
    <div class="back-brand">
      <span class="back-brand__main">KLV</span>
      <span class="back-brand__sub">ROOFING</span>
    </div>
  </section>
</main>
</body>
</html>
```